- Redesign our business card
- Logo remains unchanged
- Current business card attached

Target Market(s)

We are a property management company

Industry/Entity Type

Business

```html
<!DOCTYPE html>
<html lang="en">
<head>
<meta charset="utf-8">
<title>Marlow Property – Business Card</title>
<link href="https://fonts.googleapis.com/css2?family=Belleza&display=swap" rel="stylesheet">
<style>
  :root {
    --olive: #877f3f;
    --sand: #e0d6b4;
    --white: #ffffff;
    --card-w: 667px;
    --card-h: 1200px;
  }
  html, body {
    margin: 0;
    padding: 0;
    overflow: hidden;
    background: var(--white);
  }
  .card {
    position: relative;
    width: var(--card-w);
    height: var(--card-h);
    background: var(--white);
    font-family: "Belleza", sans-serif;
    color: var(--olive);
    overflow: hidden;
  }
  .line {
    position: absolute;
    left: 0;
    width: 100%;
    text-align: center;
    white-space: nowrap;
    line-height: 1;
  }
  .services { font-size: 41px; }
  .services--strata { top: 36px; }
  .services--community { top: 122px; }
  .services--property { top: 206px; }

  .brand {
    position: absolute;
    top: 370px;
    left: 0;
    width: 100%;
    display: flex;
    justify-content: center;
    align-items: center;
    gap: 18px;
    font-size: 52px;
    letter-spacing: 1px;
  }
  .brand__square {
    width: 40px;
    height: 40px;
    background: var(--olive);
  }

  .manager-name { top: 563px; font-size: 41px; letter-spacing: 0.5px; }
  .manager-title { top: 614px; font-size: 33px; color: var(--sand); }

  .address { font-size: 30px; letter-spacing: 0.5px; }
  .address--postal-1 { top: 694px; }
  .address--postal-2 { top: 739px; }
  .address--street-1 { top: 795px; }
  .address--street-2 { top: 843px; }

  .contact { font-size: 32px; letter-spacing: 0.5px; }
  .contact__label { color: var(--sand); }
  .contact--tel { top: 898px; }
  .contact--fax { top: 947px; }
  .contact--mobile { top: 992px; }
  .contact--email { top: 1050px; font-size: 30px; letter-spacing: 0; }

  .web-band {
    position: absolute;
    left: 0;
    top: 1124px;
    width: 100%;
    height: 76px;
    background: var(--olive);
    color: var(--white);
    display: flex;
    align-items: center;
    justify-content: center;
    font-size: 32px;
  }
</style>
</head>
<body>
  <div class="card">
    <div class="line services services--strata">Strata Management</div>
    <div class="line services services--community">Community Management</div>
    <div class="line services services--property">Property Management</div>

    <div class="brand">
      <span class="brand__square"></span>
      <span class="brand__name">MARLOW PROPERTY</span>
    </div>

    <div class="line manager-name">DANIEL HARTLEY</div>
    <div class="line manager-title">Licensed Strata Manager</div>

    <div class="line address address--postal-1">PO BOX 48,</div>
    <div class="line address address--postal-2">BAYVIEW HILLS NSW 2090</div>
    <div class="line address address--street-1">12/5-19 LINDEN STREET</div>
    <div class="line address address--street-2">PARKVALE NSW 2091</div>

    <div class="line contact contact--tel"><span class="contact__label">T:</span> 02 9000 4127</div>
    <div class="line contact contact--fax"><span class="contact__label">F:</span> 02 9000 4128</div>
    <div class="line contact contact--mobile"><span class="contact__label">M:</span> 0400 318 672</div>
    <div class="line contact contact--email">info@marlowproperty.com.au</div>

    <div class="web-band">www.marlowproperty.com.au</div>
  </div>
</body>
</html>
```